Business cards for Harbourline Supply Pty Ltd that import building products into Australia from China
Target Market(s)
Business to Business
Industry/Entity Type
Business
Contact Information for Business Card
Front: Logo and Business Name
Rear:
Desmond Varrick
General Manager
Mobile: 0427 561 394
email: dessie@harbourlinesupply.com.au
alternative email: dessie@outbackworks.com.au
web: www.harbourlinesupply.com.au
Adelaide, Brisbane and Darwin
Colors
ec1f27
fbee3d

```html
<!DOCTYPE html>
<html lang="en">
<head>
<meta charset="utf-8">
<title>Harbourline Supply Pty Ltd – Business Cards</title>
<link href="https://fonts.googleapis.com/css2?family=Montserrat:wght@400;500;700&display=swap" rel="stylesheet">
<style>
  :root {
    --brand-red: #ec1f27;
    --brand-yellow: #fbee3d;
    --card-black: #050505;
    --stage: #3a3a3a;
    --text-white: #ffffff;
  }
  * { box-sizing: border-box; margin: 0; padding: 0; }
  html, body { width: 1200px; height: 864px; overflow: hidden; }
  body {
    background: var(--stage);
    font-family: "Montserrat", sans-serif;
    display: flex;
    flex-direction: column;
    align-items: center;
    justify-content: center;
    gap: 40px;
  }
  .card {
    width: 660px;
    height: 377px;
    background: var(--card-black);
    border-radius: 22px;
    position: relative;
    box-shadow: 0 10px 30px rgba(0,0,0,0.45);
    color: var(--text-white);
  }
  .wordmark {
    display: flex;
    align-items: center;
    gap: 14px;
  }
  .wordmark__square {
    width: 22px;
    height: 22px;
    background: var(--brand-yellow);
    flex: none;
  }
  .wordmark__name {
    color: var(--brand-red);
    font-weight: 700;
    font-size: 30px;
    line-height: 1.05;
    letter-spacing: 1px;
    text-transform: uppercase;
  }

  /* Front */
  .card--front .wordmark {
    position: absolute;
    left: 50%;
    top: 128px;
    transform: translateX(-50%);
  }
  .card--front .cities {
    position: absolute;
    left: 0; right: 0;
    bottom: 60px;
    text-align: center;
    font-size: 15px;
    font-weight: 500;
    letter-spacing: 0.5px;
  }
  .cities__dot { color: var(--brand-red); margin: 0 6px; }

  /* Back */
  .card--back .wordmark {
    position: absolute;
    left: 50px;
    top: 158px;
  }
  .card--back .wordmark__name { font-size: 24px; }
  .divider {
    position: absolute;
    left: 330px;
    top: 72px;
    width: 2px;
    height: 190px;
    background: var(--brand-red);
  }
  .contact {
    position: absolute;
    left: 356px;
    top: 76px;
  }
  .contact__name {
    color: var(--brand-red);
    font-weight: 700;
    font-size: 22px;
  }
  .contact__title {
    font-size: 15px;
    font-weight: 500;
    margin-top: 2px;
    margin-bottom: 26px;
  }
  .contact__list { list-style: none; }
  .contact__item {
    display: flex;
    align-items: center;
    gap: 10px;
    font-size: 13.5px;
    line-height: 1.85;
  }
  .contact__icon { width: 15px; height: 15px; flex: none; }
</style>
</head>
<body>

  <section class="card card--front" aria-label="Card front">
    <div class="wordmark">
      <span class="wordmark__square"></span>
      <span class="wordmark__name">Harbourline Supply<br>Pty Ltd</span>
    </div>
    <p class="cities">Adelaide<span class="cities__dot">•</span>Brisbane<span class="cities__dot">•</span>Darwin</p>
  </section>

  <section class="card card--back" aria-label="Card back">
    <div class="wordmark">
      <span class="wordmark__square"></span>
      <span class="wordmark__name">Harbourline<br>Supply<br>Pty Ltd</span>
    </div>
    <div class="divider"></div>
    <div class="contact">
      <p class="contact__name">Desmond Varrick</p>
      <p class="contact__title">General Manager</p>
      <ul class="contact__list">
        <li class="contact__item">
          <svg class="contact__icon" viewBox="0 0 16 16" aria-hidden="true"><rect x="4" y="1" width="8" height="14" rx="1.5" fill="none" stroke="#fbee3d" stroke-width="1.6"/><circle cx="8" cy="12.3" r="0.9" fill="#fbee3d"/></svg>
          0427 561 394
        </li>
        <li class="contact__item">
          <svg class="contact__icon" viewBox="0 0 16 16" aria-hidden="true"><rect x="1" y="3" width="14" height="10" fill="#fbee3d"/><path d="M1 3 L8 9 L15 3" fill="none" stroke="#050505" stroke-width="1.3"/></svg>
          dessie@harbourlinesupply.com.au
        </li>
        <li class="contact__item">
          <svg class="contact__icon" viewBox="0 0 16 16" aria-hidden="true"><rect x="1" y="3" width="14" height="10" fill="#fbee3d"/><path d="M1 3 L8 9 L15 3" fill="none" stroke="#050505" stroke-width="1.3"/></svg>
          dessie@outbackworks.com.au
        </li>
        <li class="contact__item">
          <svg class="contact__icon" viewBox="0 0 16 16" aria-hidden="true"><g fill="none" stroke="#fbee3d" stroke-width="1.3"><circle cx="8" cy="8" r="6.5"/><ellipse cx="8" cy="8" rx="2.8" ry="6.5"/><path d="M1.5 8 H14.5 M2.5 4.8 H13.5 M2.5 11.2 H13.5"/></g></svg>
          www.harbourlinesupply.com.au
        </li>
      </ul>
    </div>
  </section>

</body>
</html>
```